"Thornbury Accupuncture" needs a Promotional Card - A6 size

Requirements
Must have
• Bright colours, pictures of happy people, acupuncture-related pictures.

```html
<!DOCTYPE html>
<html lang="en">
<head>
<meta charset="utf-8">
<title>Thornbury Accupuncture – Card Design</title>
<link href="https://fonts.googleapis.com/css2?family=Raleway:wght@300;400;500;600;700;800&display=swap" rel="stylesheet">
<style>
:root{
  --board:#e9e9e9;
  --red:#e8432a;
  --red-text:#e4472b;
  --yellow:#fdd04d;
  --cream:#fff8e6;
  --ink:#222;
}
*{margin:0;padding:0;box-sizing:border-box}
html,body{width:1200px;height:1000px;overflow:hidden}
body{background:var(--board);font-family:"Raleway",sans-serif;position:relative}
.topbar{position:absolute;left:0;top:0;width:1200px;height:57px;background:linear-gradient(#fafafa,#dcdcdc);box-shadow:0 2px 4px rgba(0,0,0,.2)}
.topbar .project{position:absolute;left:27px;top:15px;font-weight:700;font-size:22px;color:var(--ink)}
.topbar .kind{position:absolute;right:28px;top:14px;font-weight:400;font-size:24px;color:var(--ink)}
.label{position:absolute;top:908px;font-size:22px;color:var(--ink);width:300px;text-align:center}
.card{position:absolute;top:115px;width:536px;height:754px;overflow:hidden;box-shadow:0 2px 8px rgba(0,0,0,.25);color:var(--red-text)}
.card svg.bg{position:absolute;left:0;top:0}
.card > *:not(svg){position:absolute}
.front{left:47px}
.back{left:612px}
.brand{font-weight:700;color:var(--red);text-align:center;line-height:1}
.front .brand{left:318px;top:257px;width:200px;font-size:19px}
.front .headline{left:0;width:536px;top:311px;text-align:center;font-weight:800;font-size:23px;color:var(--red)}
.front .subline{left:0;width:536px;top:340px;text-align:center;font-size:18px;font-weight:400}
.rule{height:2px;background:var(--red)}
.front .rule{left:40px;width:457px;top:370px}
.front .question{left:0;width:536px;top:383px;text-align:center;font-size:20px;font-weight:600}
.symptoms{left:0;width:536px;top:412px;font-size:16px;font-weight:600;line-height:20.5px}
.symptoms li{list-style:none;display:flex}
.symptoms .a{width:236px;text-align:right}
.symptoms .dot{width:27px;text-align:center}
.front .intro{left:40px;width:458px;top:533px;font-size:13.5px;line-height:17.3px;font-weight:500}
.intro b{font-weight:700}
.cta{left:0;width:536px;top:618px;height:92px;background:var(--red);color:#fff;text-align:center;font-weight:800;font-size:18px;line-height:24px;padding-top:10px}
.foot{left:0;width:536px;top:710px;height:44px;font-size:12px;font-weight:500;padding:0 28px;display:flex;justify-content:space-between;align-items:center}
.back .about{left:40px;top:143px;font-size:34px;font-weight:400;line-height:1}
.about b{font-weight:700}
.back .rule.r1{left:40px;width:291px;top:183px}
.bio{left:41px;width:292px;top:195px;font-size:14.5px;line-height:18.3px;text-align:justify;font-weight:500}
.portrait{left:353px;top:125px;width:165px;height:205px;border-radius:60px 60px 0 0;background:linear-gradient(#4a3834,#7d5a63 55%,#9b6f8c)}
.back .brand{left:60px;top:480px;width:204px;font-size:24px}
.avail{left:40px;top:542px;width:236px;height:33px;background:var(--red);color:#fff;font-size:20px;font-weight:700;text-align:center;line-height:33px}
.contacts{left:55px;top:588px;font-size:14px;font-weight:500;list-style:none}
.contacts li{display:flex;align-items:center;height:30.5px}
.contacts svg{margin-right:9px}
.whatis{left:291px;width:200px;top:383px;text-align:center;font-size:26px;font-weight:300;letter-spacing:3px;line-height:1}
.whatis-b{left:291px;width:200px;top:410px;text-align:center;font-size:24px;font-weight:800;line-height:1}
.back .rule.r2{left:291px;width:200px;top:441px}
.explain{left:291px;width:200px;top:451px;font-size:14px;line-height:17.2px;text-align:justify;font-weight:500}
.explain p{margin-bottom:7px}
</style>
</head>
<body>
<header class="topbar">
  <div class="project">THORNBURY ACCUPUNCTURE</div>
  <div class="kind">Card Design</div>
</header>

<section class="card front">
  <svg class="bg" width="536" height="754" viewBox="0 0 536 754">
    <defs>
      <linearGradient id="frontBase" x1="0" y1="0" x2="0" y2="1">
        <stop offset=".3" stop-color="#ffffff"/>
        <stop offset=".65" stop-color="#fee9b2"/>
        <stop offset="1" stop-color="#fdd25a"/>
      </linearGradient>
      <linearGradient id="photoTone" x1="0" y1="0" x2="1" y2="1">
        <stop offset="0" stop-color="#f4ede4"/>
        <stop offset=".45" stop-color="#e9b06a"/>
        <stop offset="1" stop-color="#f6c36a"/>
      </linearGradient>
    </defs>
    <rect width="536" height="754" fill="url(#frontBase)"/>
    <g role="img" aria-label="Photograph of a smiling senior couple and a woman easing a sore neck">
      <path d="M0 0H536V185C420 180 300 200 250 240C200 275 100 280 0 270Z" fill="url(#photoTone)"/>
    </g>
    <path d="M0 110C80 130 160 200 205 262C140 276 70 276 0 270Z" fill="#e8732a" opacity=".65"/>
    <path d="M160 0C230 60 250 150 250 240C290 210 330 195 380 188C330 120 250 40 180 0Z" fill="#c7781f" opacity=".45"/>
    <path d="M330 0C420 30 500 90 536 150V0Z" fill="#fde08a" opacity=".75"/>
    <rect y="710" width="536" height="44" fill="var(--yellow)"/>
  </svg>
  <div class="brand">thornbury<br>accupuncture</div>
  <h1 class="headline">CHINESE MEDICINE &amp; ACUPUNCTURE</h1>
  <p class="subline">CAN IMPROVE YOUR WELL-BEING</p>
  <div class="rule"></div>
  <h2 class="question">Do you suffer from any of the following?</h2>
  <ul class="symptoms">
    <li><span class="a">Anxiety</span><span class="dot">•</span><span>Stress</span></li>
    <li><span class="a">Problems Walking</span><span class="dot">•</span><span>Menopausal Symptoms</span></li>
    <li><span class="a">Chronic Pain</span><span class="dot">•</span><span>Arthritis</span></li>
    <li><span class="a">Depression</span><span class="dot">•</span><span>Headache</span></li>
    <li><span class="a">Insomnia</span><span class="dot">•</span><span>PMS</span></li>
  </ul>
  <p class="intro"><b>Mirela Kostova</b> is a qualified acupuncturist and the majority of her clients have some of the following health issues. To learn about the current research in acupuncture for the different conditions visit the National Acupuncture Board website, www.thornbury-acu.co.uk</p>
  <div class="cta">CONTACT MIRELA FOR A FREE, 15-MINUTE,<br>NO-OBLIGATION CONSULTATION &amp; FIND OUT<br>HOW ACUPUNCTURE CAN HELP YOU.</div>
  <div class="foot"><span>www.thornbury-acu.co.uk</span><span>Tel No.: (02) 987 654 3210</span></div>
</section>

<section class="card back">
  <svg class="bg" width="536" height="754" viewBox="0 0 536 754">
    <defs>
      <linearGradient id="backBase" x1="0" y1="0" x2="0" y2="1">
        <stop offset="0" stop-color="#fdf0cf"/>
        <stop offset="1" stop-color="#fde7ad"/>
      </linearGradient>
      <linearGradient id="backLower" x1="0" y1="0" x2="0" y2="1">
        <stop offset="0" stop-color="#ffffff"/>
        <stop offset=".45" stop-color="#fff3d3"/>
        <stop offset="1" stop-color="#fdd04f"/>
      </linearGradient>
    </defs>
    <rect width="536" height="754" fill="#fde2a4"/>
    <path d="M0 0H300C230 10 120 10 0 25Z" fill="#fff"/>
    <path d="M0 25C140 5 300 40 375 158L360 168C290 70 150 45 0 85Z" fill="#f5a85c"/>
    <path d="M430 95C470 65 505 55 536 52V205C500 165 465 130 430 95Z" fill="#eba07c"/>
    <path d="M0 85C150 62 290 100 362 165C420 185 480 155 536 135V754H0Z" fill="url(#backBase)"/>
    <path d="M0 380C150 340 350 330 536 320V754H0Z" fill="url(#backLower)"/>
  </svg>
  <h2 class="about">ABOUT <b>MIRELA</b></h2>
  <div class="rule r1"></div>
  <p class="bio">Mirela Kostova has a passion for helping people to stay healthy without the need for drugs. She graduated with a BSc (hons) from the respected Eastfield College of Oriental Medicine in Reading. Mirela also has a BSc in Physiotherapy and 9 years' experience working in the County Health Service.</p>
  <div class="portrait" role="img" aria-label="Portrait photograph of the acupuncturist"></div>
  <div class="brand">thornbury<br>accupuncture</div>
  <div class="avail">AVAIL IT NOW!</div>
  <ul class="contacts">
    <li><svg width="22" height="22" viewBox="0 0 22 22"><circle cx="11" cy="11" r="11" fill="var(--red)"/><path d="M8 6c-1 0-2 1-1.6 2.6.8 3 3.5 6 6.8 7 1.4.4 2.4-.5 2.6-1.4l-2.2-1.6-1.2 1c-1.6-.8-3-2.3-3.6-3.8l1-1.2Z" fill="#fff"/></svg>(02) 987 654 3210</li>
    <li><svg width="22" height="22" viewBox="0 0 22 22"><circle cx="11" cy="11" r="11" fill="var(--red)"/><g fill="none" stroke="#fff" stroke-width="1.2"><circle cx="11" cy="11" r="5.5"/><ellipse cx="11" cy="11" rx="2.4" ry="5.5"/><path d="M5.5 11h11"/></g></svg>www.thornbury-acu.co.uk</li>
    <li><svg width="22" height="22" viewBox="0 0 22 22"><circle cx="11" cy="11" r="11" fill="var(--red)"/></svg>thornburyacu</li>
    <li><svg width="22" height="22" viewBox="0 0 22 22"><circle cx="11" cy="11" r="11" fill="var(--red)"/></svg>@thornburyacu</li>
  </ul>
  <div class="whatis">WHAT IS</div>
  <div class="whatis-b">ACUPUNCTURE?</div>
  <div class="rule r2"></div>
  <div class="explain">
    <p>Acupuncture is a holistic therapy practised for more than 2500 years in China and now popular around the world.</p>
    <p>Specific points on the body are stimulated to assist the body's own healing ability, balancing its energy and boosting the feeling of well-being.</p>
    <p>To find out more about acupuncture, visit Mirela's website.</p>
  </div>
</section>

<div class="label" style="left:165px">Front Design</div>
<div class="label" style="left:730px">Back Design</div>
</body>
</html>
```